Website Design for recruiting company

We need a homepage mockup for a recruiting company focused on the legal industry. Use your creative talent to come up with something visually appeal and professional for this web-site.

We'd really like to see the maze from the logo incorporated into the design somehow. Please use the website mockup provided as inspiration for this project. We really like the layout and photos!

Target Market(s)

lawyers

Industry/Entity Type

Legal

Number of Pages Required

1 page

Font styles to use
Sans Serif

```html
<!DOCTYPE html>
<html lang="en">
<head>
<meta charset="utf-8">
<title>Harborline Legal Search</title>
<link href="https://fonts.googleapis.com/css2?family=Titillium+Web:wght@400;600&family=Open+Sans:wght@400&display=swap" rel="stylesheet">
<style>
:root{
  --plum:#5f5061;
  --plum-dark:#4a3e4b;
  --lilac:#ede1ea;
  --ink:#1b1b1f;
  --text:#3a3a3a;
  --muted:#6b6b6b;
  --footer:#221c23;
  --white:#ffffff;
}
*{margin:0;padding:0;box-sizing:border-box}
html,body{width:1200px;height:2553px;overflow:hidden}
body{position:relative;background:var(--white);font-family:"Open Sans",sans-serif;color:var(--text)}
.abs{position:absolute}
.display{font-family:"Titillium Web",sans-serif}

/* hero */
.hero{left:0;top:0;width:1200px;height:620px;overflow:hidden}
.hero-photo{position:absolute;inset:0;background:linear-gradient(100deg,#4d5a6a 0%,#3a4150 30%,#5b5f66 55%,#2d3440 80%,#1f2630 100%)}
.hero-shade{position:absolute;inset:0;background:linear-gradient(90deg,rgba(0,0,0,0) 40%,rgba(10,14,22,.45) 100%)}
.hero-curve{position:absolute;left:0;top:560px}
.brand{left:144px;top:12px;display:flex;align-items:center;gap:10px}
.brand-dot{width:78px;height:78px;border-radius:50%;border:3px solid #e8e6e2;background:rgba(255,255,255,.08)}
.brand-name{font-family:"Titillium Web",sans-serif;font-size:14px;color:#e8e6e2}
.nav{right:135px;top:35px;display:flex;gap:14px}
.nav a{font-family:"Titillium Web",sans-serif;font-size:16px;color:var(--white);text-decoration:none;padding:3px 10px;border-radius:2px}
.nav a.active{background:var(--plum)}
.hero-copy{right:135px;top:245px;text-align:right;color:var(--white)}
.hero-title{font-size:58px;font-weight:400;line-height:1}
.hero-sub{font-size:31px;margin-top:6px;line-height:1.1}
.hero-actions{margin-top:16px;display:flex;justify-content:flex-end;gap:17px}
.btn-light{background:var(--white);color:var(--ink);font-family:"Titillium Web",sans-serif;font-size:16px;padding:0 18px;height:44px;line-height:44px;border-radius:2px}
.arrow{top:305px}
.scroll-dot{left:576px;top:591px;width:48px;height:48px;border-radius:50%;background:#e4e2e4;display:flex;align-items:center;justify-content:center}

/* welcome */
.section-title{font-family:"Titillium Web",sans-serif;font-size:32px;font-weight:600;color:var(--ink);line-height:40px}
.rule{height:3px;width:120px;background:var(--plum)}
.welcome-title{left:144px;top:712px}
.welcome-rule{left:144px;top:814px}
.welcome-text{left:144px;top:840px;width:435px;font-size:16px;line-height:32px;color:var(--text)}
.welcome-photo{left:646px;top:718px;width:409px;height:342px;background:linear-gradient(135deg,#8c8679 0%,#5f574c 45%,#a58058 75%,#6d5037 100%)}
.welcome-mark{left:934px;top:943px;width:162px;height:162px;border-radius:50%;background:#d9d9d3;border:6px solid #ededE8}

/* news */
.news{left:0;top:1165px;width:1200px;height:810px;background:var(--lilac)}
.news-title{left:0;width:1200px;top:1243px;text-align:center}
.news-rule{left:540px;top:1305px}
.news-intro{left:0;width:1200px;top:1337px;text-align:center;font-size:16px;color:var(--ink)}
.card{top:1388px;width:224px;height:375px;background:var(--white)}
.card-photo{position:absolute;left:8px;top:8px;width:208px;height:160px}
.avatar{position:absolute;left:24px;top:138px;width:60px;height:60px;border-radius:50%;border:3px solid var(--white);background:linear-gradient(160deg,#c9b7a6,#6f655e)}
.card-title{position:absolute;left:12px;top:215px;width:205px;font-size:14px;line-height:19px;color:var(--ink)}
.card-text{position:absolute;left:12px;top:256px;width:205px;font-size:9.5px;line-height:16px;color:var(--muted)}
.btn-plum{background:var(--plum);color:var(--white);font-family:"Titillium Web",sans-serif;font-size:15px;text-align:center}
.card .btn-plum{position:absolute;left:12px;top:319px;width:96px;height:32px;line-height:32px}
.btn-search{left:536px;top:1798px;width:128px;height:44px;line-height:44px;background:#2a2a2c;color:var(--white);font-family:"Titillium Web",sans-serif;font-size:16px;text-align:center;border-radius:2px}
.news-curve{left:0;top:1920px}

/* employers */
.emp-mark{left:458px;top:2045px;width:284px;height:284px;border-radius:50%;background:#f1f0ee}
.emp-title{left:0;width:1200px;top:2087px;text-align:center}
.emp-rule{left:540px;top:2142px}
.emp-text{left:144px;width:912px;top:2168px;text-align:center;font-size:16px;line-height:29px;color:var(--ink)}
.emp-actions{left:368px;top:2243px;display:flex;gap:17px}
.emp-actions .btn-plum{width:224px;height:44px;line-height:44px;font-size:16px}

/* footer */
.footer{left:0;top:2390px;width:1200px;height:163px}
.footer-links{left:144px;top:2460px;font-size:11.5px;color:#b9aeb8}
.footer-links span{margin:0 9px}
.footer-copy{left:144px;top:2493px;font-size:11.5px;color:#b9aeb8}
.social{left:945px;top:2476px;display:flex;gap:26px}
.social i{display:block;width:20px;height:20px;border-radius:50%;background:#8a7f8a}
</style>
</head>
<body>

<header class="abs hero">
  <div class="hero-photo" role="img" aria-label="Smiling attorney in a grey suit talking across a desk with a candidate"></div>
  <div class="hero-shade"></div>
  <svg class="hero-curve" width="1200" height="60" viewBox="0 0 1200 60">
    <path d="M0 10 Q600 70 1200 10 L1200 60 L0 60 Z" fill="#5f5061"/>
    <path d="M0 30 Q600 70 1200 30 L1200 60 L0 60 Z" fill="#ffffff"/>
  </svg>
</header>

<div class="abs brand"><div class="brand-dot"></div><span class="brand-name">harborline legal search</span></div>

<nav class="abs nav">
  <a class="active" href="#">HOME</a><a href="#">ABOUT US</a><a href="#">WHAT'S NEW</a><a href="#">FOR EMPLOYERS</a><a href="#">CONTACT US</a>
</nav>

<svg class="abs arrow" style="left:52px" width="22" height="32" viewBox="0 0 22 32"><path d="M16 4 L6 16 L16 28" fill="none" stroke="#fff" stroke-width="4"/></svg>
<svg class="abs arrow" style="left:1124px" width="22" height="32" viewBox="0 0 22 32"><path d="M6 4 L16 16 L6 28" fill="none" stroke="#fff" stroke-width="4"/></svg>

<div class="abs hero-copy display">
  <h1 class="hero-title">START HERE,</h1>
  <p class="hero-sub">Let Our Experience Guide You</p>
  <div class="hero-actions"><span class="btn-light">FIND A JOB</span><span class="btn-light">FIND A POSITION</span></div>
</div>

<div class="abs scroll-dot"><svg width="14" height="22" viewBox="0 0 14 22"><rect x="1" y="1" width="12" height="20" rx="6" fill="#333"/><rect x="6" y="4" width="2" height="5" fill="#e4e2e4"/></svg></div>

<section>
  <h2 class="abs section-title welcome-title">WELCOME TO<br>HARBORLINE LEGAL SEARCH</h2>
  <div class="abs rule welcome-rule"></div>
  <p class="abs welcome-text">Harborline Legal Search focuses on the permanent placement of attorneys with law firms and corporations in the New England area. Founded in 1982, Harborline Legal Search is the oldest attorney search firm in New England, and is ranked the number one legal recruiter in New England in the most recent survey conducted by The Counsel Review.</p>
  <div class="abs welcome-photo" role="img" aria-label="Two professionals shaking hands across a meeting table"></div>
  <div class="abs welcome-mark"></div>
</section>

<section>
  <div class="abs news"></div>
  <h2 class="abs section-title news-title">WHAT'S NEW</h2>
  <div class="abs rule news-rule"></div>
  <p class="abs news-intro">Below are our most recent listings. All positions are in the greater Boston area unless otherwise noted.</p>

  <article class="abs card" style="left:0">
    <div class="card-photo" role="img" aria-label="Attorney in a suit in front of a law library" style="background:linear-gradient(135deg,#6b3a22,#2b1f1c 50%,#8a5a36)"></div>
    <div class="avatar" role="img" aria-label="Recruiter portrait"></div>
    <h3 class="card-title">Etiam vel massa elementum, bibendum tellus</h3>
    <p class="card-text">Pellentesque convallis molestie enim sit amet efficitur. Etiam id imperdiet lectus. Vivamus lacus justo, ultrices nec erat.</p>
    <div class="btn-plum">APPLY NOW</div>
  </article>
  <article class="abs card" style="left:244px">
    <div class="card-photo" role="img" aria-label="Woman on the phone at an office desk" style="background:linear-gradient(135deg,#9fb0bf,#3f6f8f 50%,#c7ccd2)"></div>
    <div class="avatar" role="img" aria-label="Recruiter portrait"></div>
    <h3 class="card-title">Pellentesque a imperdiet dolor, et auctor est</h3>
    <p class="card-text">Pellentesque convallis molestie enim sit amet efficitur. Etiam id imperdiet lectus. Vivamus lacus justo, ultrices nec erat.</p>
    <div class="btn-plum">APPLY NOW</div>
  </article>
  <article class="abs card" style="left:488px">
    <div class="card-photo" role="img" aria-label="Woman working on a laptop in a bright office" style="background:linear-gradient(135deg,#e6e6e4,#c9c4bd 50%,#f2f2f0)"></div>
    <div class="avatar" role="img" aria-label="Recruiter portrait"></div>
    <h3 class="card-title">Fusce sollicitudin lorem et luctus volutpat</h3>
    <p class="card-text">Pellentesque convallis molestie enim sit amet efficitur. Etiam id imperdiet lectus. Vivamus lacus justo, ultrices nec erat.</p>
    <div class="btn-plum">APPLY NOW</div>
  </article>
  <article class="abs card" style="left:732px">
    <div class="card-photo" role="img" aria-label="Two colleagues in conversation at a table" style="background:linear-gradient(135deg,#4a4644,#8d8680 50%,#2f2c2b)"></div>
    <div class="avatar" role="img" aria-label="Recruiter portrait"></div>
    <h3 class="card-title">Etiam vel massa elementum, bibendum tellus venenatis,</h3>
    <p class="card-text">Pellentesque convallis molestie enim sit amet efficitur. Etiam id imperdiet lectus. Vivamus lacus justo, ultrices nec erat.</p>
    <div class="btn-plum">APPLY NOW</div>
  </article>
  <article class="abs card" style="left:976px">
    <div class="card-photo" role="img" aria-label="Team meeting around a conference table" style="background:linear-gradient(135deg,#bcc8d2,#5d6f80 50%,#d8dde1)"></div>
    <div class="avatar" role="img" aria-label="Recruiter portrait"></div>
    <h3 class="card-title">Curabitur venenatis lacinia ornare. Cras sollicitudin</h3>
    <p class="card-text">Pellentesque convallis molestie enim sit amet efficitur. Etiam id imperdiet lectus. Vivamus lacus justo, ultrices nec erat.</p>
    <div class="btn-plum">APPLY NOW</div>
  </article>

  <div class="abs btn-search">SEARCH JOBS</div>
  <svg class="abs news-curve" width="1200" height="60" viewBox="0 0 1200 60">
    <path d="M0 5 Q600 75 1200 5 L1200 60 L0 60 Z" fill="#5f5061"/>
    <path d="M0 25 Q600 75 1200 25 L1200 60 L0 60 Z" fill="#ffffff"/>
  </svg>
</section>

<section>
  <div class="abs emp-mark"></div>
  <h2 class="abs section-title emp-title">FOR EMPLOYERS</h2>
  <div class="abs rule emp-rule"></div>
  <p class="abs emp-text">Our unparalleled recruiting industry and legal experience have generated an extensive network of contacts throughout the legal community.</p>
  <div class="abs emp-actions"><div class="btn-plum">START HERE</div><div class="btn-plum">FIND THE RIGHT CANDIDATE</div></div>
</section>

<footer>
  <svg class="abs footer" width="1200" height="163" viewBox="0 0 1200 163">
    <path d="M0 30 Q600 -15 1200 30 L1200 163 L0 163 Z" fill="#5f5061"/>
    <path d="M0 50 Q600 -5 1200 50 L1200 163 L0 163 Z" fill="#221c23"/>
  </svg>
  <p class="abs footer-links">Home<span>|</span>About Us<span>|</span>What's New<span>|</span>For Employers<span>|</span>Contact Us</p>
  <p class="abs footer-copy">Copyright © 2020 &nbsp; Harborline Legal Search, All rights reserved</p>
  <div class="abs social"><i aria-label="Social link"></i><i aria-label="Social link"></i><i aria-label="Social link"></i></div>
</footer>

</body>
</html>
```